Brand refresh of quote, work docket and Fire certificate documents

I would like a refresh of our document suit including

1. Front page called MURO6 Proposal
2. Quote document template
3. Work docket template
4. Fire certificate template - to look like a professional complaint certificate

Examples of documents are attached.

```html
<!DOCTYPE html>
<html lang="en">
<head>
<meta charset="utf-8">
<title>MURO6 Document Suite</title>
<link rel="stylesheet" href="https://fonts.googleapis.com/css2?family=Open+Sans:ital,wght@0,400;0,600;0,700;0,800;1,400&display=swap">
<style>
:root{
  --black:#000;
  --red:#d0202a;
  --orange:#f08a24;
  --orange-bright:#f7941d;
  --cream:#faf6ee;
  --ink:#222;
  --grey:#555;
  --line:#ddd;
  --bar:linear-gradient(90deg,#d0202a,#f08a24);
}
*{box-sizing:border-box;margin:0;padding:0}
html,body{width:1200px;height:2400px;overflow:hidden;background:#fff;font-family:'Open Sans',sans-serif;color:var(--ink)}
.canvas{position:relative;width:1200px;height:2400px}
.section-title{position:absolute;left:0;width:1200px;text-align:center;font-weight:700;font-size:26px;text-decoration:underline;text-underline-offset:5px;text-decoration-thickness:2px}
.sheet{position:absolute;width:454px;height:641px;box-shadow:0 8px 18px rgba(0,0,0,.18);overflow:hidden}

/* Brand wordmark */
.brand{font-weight:800;color:#fff;letter-spacing:1px;line-height:1}
.brand-mark{display:inline-block;width:.35em;height:.35em;background:var(--orange);margin-left:.15em;vertical-align:top}
.tagline{color:#fff;letter-spacing:3px;font-size:9px}

/* Cover */
.cover{left:373px;top:134px;background:var(--black)}
.cover .brand{position:absolute;top:52px;width:100%;text-align:center;font-size:56px}
.cover .tagline{position:absolute;top:106px;width:100%;text-align:center}
.cover .pill{position:absolute;left:130px;top:130px;width:194px;height:26px;border-radius:13px;background:var(--orange-bright);color:#fff;font-size:14px;letter-spacing:3px;text-align:center;line-height:26px}
.cover svg{position:absolute;left:0;top:178px}
.cover .url{position:absolute;bottom:27px;width:100%;text-align:center;color:#fff;font-size:12px;font-weight:600;letter-spacing:.5px}

/* Docket */
.docket{background:#fff;font-size:8.6px;color:var(--ink)}
.docket-left{left:137px;top:915px}
.docket-right{left:608px;top:915px}
.doc-head{height:71px;background:var(--black);position:relative}
.doc-head .brand{position:absolute;left:20px;top:22px;font-size:34px}
.doc-head .tagline{position:absolute;left:20px;top:58px;font-size:5.5px;letter-spacing:2px}
.doc-head .company{position:absolute;right:18px;top:10px;text-align:right;color:#fff;font-size:8.4px;line-height:11px}
.doc-body{padding:20px 30px 0 31px}
.doc-body p{line-height:11px}
.docket-right .doc-body{padding-top:33px}
.date{margin-bottom:9px}
.docket-no{font-size:11px;font-weight:700;margin:15px 0 5px}
.area-bar{height:20px;width:393px;border-radius:0 10px 10px 0;background:var(--bar);color:#fff;font-weight:700;font-size:8.6px;line-height:20px;padding-left:9px;margin-top:6px}
.item{padding-left:10px;margin-top:8px;line-height:11px}
.trade{padding-left:10px;margin-top:6px;color:var(--red);font-style:italic}
.q{color:var(--red);font-style:italic;margin-left:8px}
.rule{border-top:1px solid var(--line);width:393px;margin:16px 0 12px}
.sub-head{color:var(--red);font-weight:700;font-size:10.5px;padding-left:10px}
.row{display:flex;padding-left:10px;margin-top:6px}
.price{font-weight:700;text-align:right}
.materials{position:relative}
.mat-list{width:200px}
.mat-list .row{justify-content:space-between}
.breakdown{position:absolute;left:210px;top:0;width:193px;height:115px;border:1px solid var(--line);border-radius:8px;background:#f7f7f7;padding:14px 12px}
.breakdown .sub-head{padding-left:0;margin-bottom:4px}
.breakdown p{margin-top:6px}
.total{display:flex;margin-top:30px;height:20px;font-weight:700;font-size:10.5px}
.total .label{width:243px;background:var(--bar);color:#fff;text-align:center;line-height:20px;border-radius:10px 0 0 10px}
.total .amount{width:146px;margin-left:4px;background:var(--black);color:var(--orange-bright);text-align:center;line-height:20px;border-radius:0 10px 10px 0}

/* Certificate */
.certificate{left:374px;top:1698px;height:639px;background:linear-gradient(180deg,#cf1f2a,#f08a24);padding:16px}
.cert-inner{width:100%;height:100%;background:var(--cream);text-align:center;padding-top:14px;color:var(--ink);overflow:hidden}
.cert-address{font-size:6.5px;line-height:8px}
.certificate .brand{color:#333;font-size:50px;margin-top:14px}
.certificate .tagline{color:#333;font-size:9px;margin-top:3px}
.cert-title{color:var(--red);font-weight:800;font-size:27px;line-height:32px;margin-top:12px}
.cert-label{color:var(--red);font-size:10px;margin-top:10px}
.cert-value{font-weight:700;font-size:16px;line-height:19px}
.cert-no{display:inline-block;margin-top:10px;background:var(--orange-bright);color:#222;font-weight:700;font-size:8.5px;padding:4px 12px;border-radius:10px}
.cert-text{font-size:8.6px;line-height:10.5px;margin:10px auto 0;width:340px}
.sign-label{font-weight:700;font-size:8.6px;margin-top:10px}
.sign-line{display:block;margin:2px auto 0}
.sign-value{font-size:8.6px}
.cert-url{color:var(--red);font-size:6.5px;margin-top:10px}
</style>
</head>
<body>
<div class="canvas">

  <h2 class="section-title" style="top:52px">Cover Page</h2>
  <section class="sheet cover">
    <div class="brand">MURO6<span class="brand-mark"></span></div>
    <div class="tagline">PASSIVE FIRE PROTECTION</div>
    <div class="pill">MURO6 PROPOSAL</div>
    <svg width="454" height="400" viewBox="0 0 454 400">
      <defs>
        <linearGradient id="coverFill" x1="0" y1="0" x2="0" y2="1">
          <stop offset="0" stop-color="#d62a2a"/>
          <stop offset=".45" stop-color="#f06a3a"/>
          <stop offset="1" stop-color="#f7941d"/>
        </linearGradient>
      </defs>
      <path d="M0 0 H336 A54 54 0 0 1 390 54 V346 A54 54 0 0 1 336 400 H0 Z" fill="#fff"/>
      <path d="M0 18 H330 A42 42 0 0 1 372 60 V340 A42 42 0 0 1 330 382 H0 Z" fill="url(#coverFill)" role="img" aria-label="Photograph of a site inspector in hard hat and hi-vis vest holding a tablet, seen from above on a concrete floor"/>
    </svg>
    <div class="url">WWW.MURO6.EXAMPLE</div>
  </section>

  <h2 class="section-title" style="top:833px">Work Docket</h2>
  <section class="sheet docket docket-left">
    <header class="doc-head">
      <div class="brand">MURO6<span class="brand-mark"></span></div>
      <div class="tagline">PASSIVE FIRE PROTECTION</div>
      <div class="company"><b>MURO6 Pty Ltd</b><br>4/27 Larkspur Road<br>Fernmoor VIC 3190<br>ABN: 00 000 000 000<br>office@muro6.example</div>
    </header>
    <div class="doc-body">
      <p class="date">26th October, 2023</p>
      <p><b>Rovella Builders</b><br>418 Tidewell St<br>Harbourvale VIC 3299<br><b>Marco</b></p>
      <p class="docket-no">Work Docket: 1188</p>
      <p>Works completed at <b>36 Calder Lane, Ashgrove Park</b> as directed by <b>Marco</b> of <b>Rovella Builders</b> as listed below.</p>
      <p style="font-weight:700;margin:7px 0 4px">Works Completed:</p>
      <div class="area-bar">Basement 1 – Fan Room</div>
      <p class="item">1 x 20mm x 20mm penetration with conduit through blockwork wall <span class="q">(?)</span></p>
      <div class="area-bar" style="margin-top:9px">Basement 1 – Apartment 38 Garage</div>
      <p class="item">2 x 100mm x 100mm penetration with sprinkler pipe &amp; wrap through slab wall.</p>
      <p class="trade">(Wet Fire)</p>
      <div class="area-bar">Basement 1 – Apartment 34 Garage</div>
      <p class="item">2 x 100mm x 100mm penetration with sprinkler pipe &amp; wrap through slab wall.</p>
      <p class="trade">(Wet Fire)</p>
      <div class="area-bar">Basement 1 – Apartment 30 Garage</div>
      <p class="item">2 x 100mm x 100mm penetration with sprinkler pipe &amp; wrap through slab wall.</p>
      <p class="trade">(Wet Fire)</p>
      <div class="area-bar">Basement 1 – Apartment 28</div>
      <p class="item">5mtrs of caulking through slab wall (one side only)</p>
      <p class="trade">(Brickies)</p>
      <div class="area-bar">Basement 1 – Apartment 28</div>
      <p class="item">5mtrs of caulking through slab wall (one side only)</p>
      <p class="trade">(Brickies)</p>
    </div>
  </section>

  <section class="sheet docket docket-right">
    <div class="doc-body">
      <div class="area-bar">Basement 1 – Back Stairwell</div>
      <p class="item">1 x 400mm x 400mm penetration empty through blockwork wall</p>
      <p class="trade">(Builder)</p>
      <div class="area-bar">Basement 1 – Apartment Bin Room</div>
      <p class="item">1 x 80mm x 80mm penetration with sprinkler pipe &amp; wrap through blockwork wall</p>
      <p class="trade">(Wet Fire)</p>
      <p class="item">2 x 20mm x 20mm penetration with conduit through blockwork wall <span class="q">(?)</span></p>
      <p class="item">2 x 20mm x 20mm penetration with conduit through blockwork wall <span class="q">(?)</span></p>
      <div class="area-bar" style="margin-top:8px">Basement 1 – Comms Room</div>
      <p class="item">2 x 300mm x 300mm penetration empty through slab wall</p>
      <p class="trade">(Builder)</p>
      <div class="area-bar">Basement 1 – Switchboard Room</div>
      <p class="item">1 x 400mm x 100mm penetration empty through blockwork wall</p>
      <p class="trade">(Builder)</p>
      <p class="item">12mtrs of caulking through blockwork wall (one side only)</p>
      <p class="trade">(Brickies)</p>
      <div class="rule"></div>
      <p class="sub-head">Labour</p>
      <div class="row"><span style="width:59px">21/10/23</span><span style="width:104px">2 Men x 5hrs = 10hrs</span><span class="price">$1500</span></div>
      <p style="padding-left:69px;margin-top:4px;font-style:italic;font-size:8px">(time &amp; a half rate)</p>
      <p class="sub-head" style="margin-top:10px">Materials</p>
      <div class="materials">
        <div class="mat-list">
          <div class="row"><span>1 x Fire Mortar (20kg bag)</span><span class="price">$150</span></div>
          <div class="row"><span>2 x Rod (Bundle</span><span class="price">$100</span></div>
          <div class="row"><span>15 x Caulk (Ltr)</span><span class="price">$375</span></div>
          <div class="row"><span>4 x KSL 300ml</span><span class="price">$120</span></div>
          <div class="row"><span>1 x Sealwrap 40 (Roll)</span><span class="price">$220</span></div>
          <div class="row"><span>¾ x KRX Pipewrap (Roll)</span><span class="price">$450</span></div>
        </div>
        <div class="breakdown">
          <p class="sub-head">Breakdown</p>
          <p>Conduits (unknown) 10% - 291.50 + GST</p>
          <p>Wet Fire 45% - $1,311 + GST</p>
          <p>Brickies 20% - $583 + GST</p>
          <p>Builder 25% - $728.75 + GST</p>
        </div>
      </div>
      <div class="total"><div class="label">Total Price for Labour &amp; Materials</div><div class="amount">$2,915 + GST</div></div>
    </div>
  </section>

  <h2 class="section-title" style="top:1620px">Certificate</h2>
  <section class="sheet certificate">
    <div class="cert-inner">
      <p class="cert-address">MURO6 Pty Ltd<br>PO Box 2041<br>Fernmoor VIC 3190<br>office@muro6.example</p>
      <div class="brand">MURO6<span class="brand-mark"></span></div>
      <div class="tagline">PASSIVE FIRE PROTECTION</div>
      <h3 class="cert-title">FIRE/SMOKE SYSTEM<br>CERTIFICATE</h3>
      <p class="cert-label">CLIENT</p>
      <p class="cert-value">Tallstone Constructions Pty Ltd</p>
      <p class="cert-label" style="margin-top:6px">JOB</p>
      <p class="cert-value">The Wren Bayside<br>22 Wren Street, Bayside</p>
      <span class="cert-no">CERTIFICATE NUMBER: 2264</span>
      <p class="cert-text"><b>MURO6 Pty. Ltd.</b> certifies that as part of our contracted works, we have carried out the above fire protection at <b>The Wren Bayside – 22 Wren Street, Bayside</b> as instructed <b>Sam Keller of Tallstone Constructions Pty Ltd</b></p>
      <p class="cert-text">These works have been completed and checked using the approved proprietary fire resistance tested products &amp; systems <b>as per AS1530 part 4 &amp; AS4072 part 1</b></p>
      <p class="cert-text">Any works that are modified, damaged or disturbed following completion are not covered by this certification.</p>
      <p class="cert-text">Installed in accordance with the manufacturer's specifications.</p>
      <p class="sign-label">Signed</p>
      <svg class="sign-line" width="60" height="18" viewBox="0 0 60 18"><path d="M4 14 C12 4 18 16 26 9 S40 12 46 6 L56 2" fill="none" stroke="#333" stroke-width="1"/></svg>
      <p class="sign-label" style="margin-top:0">Name</p>
      <p class="sign-value">Dale Morrow</p>
      <p class="sign-label" style="margin-top:4px">Date</p>
      <p class="sign-value">16th January, 2026</p>
      <p class="cert-url">MURO6.EXAMPLE</p>
    </div>
  </section>

</div>
</body>
</html>
```